Redesign of business card for Cedar Ridge Mechanical

We are looking for a new design for our business cards for Cedar Ridge Mechanical. We are a plumbing & HVAC construction company, operating on the West Coast of Canada and USA. Logo attached.
Industry/Entity Type
Construction - Plumbing & HVAC
Contact Information for Business Card
Name, address, phone numbers, email, website address
Look and feel
Each slider illustrates characteristics of the customer's brand and the style your logo design should communicate.

```html
<!DOCTYPE html>
<html lang="en">
<head>
<meta charset="utf-8">
<title>Cedar Ridge Mechanical – Business Card</title>
<link rel="stylesheet" href="https://fonts.googleapis.com/css2?family=Montserrat:wght@400;500;700&display=swap">
<style>
  :root {
    --canvas: #e3e4e4;
    --slate: #27353b;
    --white: #ffffff;
    --ink: #1e2a2f;
    --muted: #5d676b;
    --rule: #c9cdcf;
  }
  * { box-sizing: border-box; margin: 0; padding: 0; }
  html, body { width: 800px; height: 1200px; overflow: hidden; }
  body {
    background: var(--canvas);
    font-family: "Montserrat", Arial, sans-serif;
    display: flex;
    flex-direction: column;
    align-items: center;
    justify-content: center;
    gap: 90px;
  }
  .card {
    width: 680px;
    height: 388px;
    position: relative;
    box-shadow: 0 6px 18px rgba(0,0,0,0.12);
  }

  /* Front */
  .card-front { background: var(--slate); color: var(--white); }
  .card-front .brand-name {
    position: absolute;
    top: 150px; left: 0; right: 0;
    text-align: center;
    font-size: 30px;
    font-weight: 500;
    letter-spacing: 4px;
    text-transform: uppercase;
  }
  .web-row {
    position: absolute;
    left: 28px; right: 0; top: 320px;
    display: flex;
    align-items: center;
    gap: 10px;
    font-size: 12px;
  }
  .web-row .icon-box {
    width: 18px; height: 18px;
    background: var(--white);
    display: flex; align-items: center; justify-content: center;
  }
  .web-row .rule {
    flex: 1;
    height: 2px;
    background: var(--white);
    margin-left: 6px;
  }
  .card-front .base-band {
    position: absolute;
    left: 0; right: 0; bottom: 0;
    height: 14px;
    background: var(--white);
  }

  /* Back */
  .card-back { background: var(--white); color: var(--ink); display: flex; }
  .back-brand {
    width: 52%;
    display: flex; align-items: center; justify-content: center;
    text-align: center;
    font-size: 22px;
    font-weight: 500;
    letter-spacing: 3px;
    line-height: 1.35;
    text-transform: uppercase;
  }
  .divider {
    width: 2px;
    background: var(--ink);
    margin: 52px 0;
  }
  .contact {
    flex: 1;
    padding: 72px 0 0 0;
    position: relative;
  }
  .person { display: flex; gap: 10px; margin-bottom: 22px; margin-left: -13px; }
  .person .icon-box { margin-top: 4px; }
  .person-name { font-size: 20px; font-weight: 700; }
  .person-title { font-size: 10px; letter-spacing: 2px; color: var(--muted); margin-top: 2px; }
  .contact-list { list-style: none; }
  .contact-list li {
    display: flex;
    align-items: flex-start;
    gap: 12px;
    font-size: 11px;
    line-height: 1.45;
    margin: 0 0 12px -13px;
  }
  .icon-box {
    width: 24px; height: 24px;
    flex: none;
    background: var(--ink);
    display: flex; align-items: center; justify-content: center;
  }
  .contact-list li span { padding-top: 4px; }
</style>
</head>
<body>

  <section class="card card-front">
    <div class="brand-name">Cedar Ridge Mechanical</div>
    <div class="web-row">
      <div class="icon-box">
        <svg width="12" height="12" viewBox="0 0 12 12" fill="none" stroke="#27353b" stroke-width="1">
          <circle cx="6" cy="6" r="5"/><ellipse cx="6" cy="6" rx="2.2" ry="5"/><line x1="1" y1="6" x2="11" y2="6"/>
        </svg>
      </div>
      <span class="web-address">www.cedarridgemech.com</span>
      <div class="rule"></div>
    </div>
    <div class="base-band"></div>
  </section>

  <section class="card card-back">
    <div class="back-brand">Cedar Ridge<br>Mechanical</div>
    <div class="divider"></div>
    <div class="contact">
      <div class="person">
        <div class="icon-box">
          <svg width="14" height="14" viewBox="0 0 14 14" fill="#fff"><circle cx="7" cy="4.5" r="3"/><path d="M1.5 13.5c0-3 2.5-5 5.5-5s5.5 2 5.5 5z"/></svg>
        </div>
        <div>
          <div class="person-name">Lorem Ipsum</div>
          <div class="person-title">LOREM IPSUM</div>
        </div>
      </div>
      <ul class="contact-list">
        <li>
          <div class="icon-box">
            <svg width="12" height="12" viewBox="0 0 12 12" fill="#fff"><path d="M2.5 1l2 .3.8 2.4-1.3 1a7 7 0 0 0 3.3 3.3l1-1.3 2.4.8.3 2c-.2.6-.8 1-1.5 1C5 10.5 1.5 7 1.5 2.5c0-.7.4-1.3 1-1.5z"/></svg>
          </div>
          <span>604-555-0148</span>
        </li>
        <li>
          <div class="icon-box">
            <svg width="12" height="12" viewBox="0 0 12 12" fill="#fff"><path d="M6 .8a4 4 0 0 0-4 4c0 3 4 6.6 4 6.6s4-3.6 4-6.6a4 4 0 0 0-4-4zm0 5.5a1.5 1.5 0 1 1 0-3 1.5 1.5 0 0 1 0 3z"/></svg>
          </div>
          <span>2150 Harbor Way,<br>Suite 210, Tacoma, WA 98402</span>
        </li>
        <li>
          <div class="icon-box">
            <svg width="12" height="12" viewBox="0 0 12 12" fill="none" stroke="#fff" stroke-width="1.1"><rect x="1" y="2.5" width="10" height="7"/><path d="M1 2.5l5 4 5-4"/></svg>
          </div>
          <span>info@cedarridgemech.com</span>
        </li>
      </ul>
    </div>
  </section>

</body>
</html>
```